Tallon Electrical Business Card

We need a business card design for our family-run electrical contracting business based in Western Australia called 'Tallon Electrical'. We provide electrical services including residential, commercial and industrial. We aim for individual business cards to be made for all of our employees. We already have a company logo, which we require to be featured on the design. We would like simple, sleek and vibrant designs, which incorporate our logo and represent our business. We do not want anything involving too many graphics/images. We like the colours red, black, white and all shades of grey. The final design should communicate professionalism and trustworthiness.
We require the following contact information:
Name- Grant Pellow
EC 5871
Mobile number- 0455 870 219
Fax number (including area code)- (08) 9560 2831
Email adress- name@tallonelectrical.com.au
Electrical
- ITC Handel Bold

```html
<!DOCTYPE html>
<html lang="en">
<head>
<meta charset="utf-8">
<title>Tallon Electrical – Business Card</title>
<link rel="stylesheet" href="https://fonts.googleapis.com/css2?family=Russo+One&display=swap">
<style>
  :root {
    --red: #e3232a;
    --red-deep: #8e0b10;
    --black: #111111;
    --white: #ffffff;
    --grey-light: #e9e9e9;
  }
  html, body {
    margin: 0;
    padding: 0;
    overflow: hidden;
    background: var(--white);
  }
  .card {
    position: relative;
    width: 1200px;
    height: 741px;
    overflow: hidden;
    background: linear-gradient(180deg, var(--white) 0%, var(--white) 60%, var(--grey-light) 80%);
    font-family: "Russo One", "Arial Black", sans-serif;
    color: var(--black);
  }
  .wave {
    position: absolute;
    left: 0;
    top: 0;
  }
  .brand {
    position: absolute;
    left: 150px;
    top: 160px;
    width: 300px;
    text-align: center;
  }
  .brand-mark {
    display: block;
    width: 84px;
    height: 84px;
    margin: 0 auto 26px;
    background: var(--red);
  }
  .brand-name {
    margin: 0;
    font-size: 40px;
    line-height: 1.2;
    letter-spacing: 1px;
    color: var(--black);
    text-transform: uppercase;
  }
  .divider {
    position: absolute;
    left: 489px;
    top: 101px;
    width: 3px;
    height: 372px;
    background: var(--red);
  }
  .contact {
    position: absolute;
    left: 549px;
    top: 100px;
  }
  .person-name {
    margin: 0;
    font-size: 46px;
    line-height: 1;
    font-variant: small-caps;
  }
  .person-name .first { color: var(--red); }
  .licence {
    margin: 24px 0 0;
    font-size: 34px;
    line-height: 1;
  }
  .phone {
    margin: 112px 0 0;
    font-size: 36px;
    line-height: 1;
  }
  .phone .accent { color: var(--red); }
  .fax, .email {
    margin: 22px 0 0;
    font-size: 27px;
    line-height: 1;
    text-transform: uppercase;
  }
  .email { margin-top: 24px; font-size: 26px; }
  .services {
    position: absolute;
    left: 0;
    right: 0;
    top: 628px;
    margin: 0;
    text-align: center;
    color: var(--white);
    font-size: 36px;
    letter-spacing: 1px;
    word-spacing: 6px;
  }
  .services .sep { margin: 0 14px; }
</style>
</head>
<body>
  <main class="card">
    <svg class="wave" width="1200" height="741" viewBox="0 0 1200 741" aria-hidden="true">
      <defs>
        <radialGradient id="band-red" cx="0.5" cy="0.9" r="0.7">
          <stop offset="0" stop-color="#ec2a30"/>
          <stop offset="0.6" stop-color="#c5161c"/>
          <stop offset="1" stop-color="#7f080c"/>
        </radialGradient>
      </defs>
      <path d="M0,578 C320,600 720,548 1200,490 L1200,741 L0,741 Z" fill="#1a1a1a"/>
      <path d="M0,590 C330,612 760,570 1200,520 L1200,741 L0,741 Z" fill="url(#band-red)"/>
    </svg>

    <div class="brand">
      <span class="brand-mark"></span>
      <p class="brand-name">Tallon<br>Electrical</p>
    </div>

    <div class="divider"></div>

    <section class="contact">
      <h1 class="person-name"><span class="first">Grant</span> Pellow</h1>
      <p class="licence">EC 5871</p>
      <p class="phone">0455 <span class="accent">870 219</span></p>
      <p class="fax">Fax: (08) 9560 2831</p>
      <p class="email">name@tallonelectrical.com.au</p>
    </section>

    <p class="services">RESIDENTIAL<span class="sep">|</span>COMMERCIAL<span class="sep">|</span>INDUSTRIAL</p>
  </main>
</body>
</html>
```